Web design project for exciting Australian start-up

Background
We are looking for a creative and talented web design artist to work alongside our market leading web developer.
• You will be required to create a modern and clean design theme for our website, incorporating selected rustic colour scheme elements for our exciting Australian start-up to operate within the coffee industry.
reoccurring work to be expected to flow to the successful designer.
Requirements
• c. 5 - 10 page website
• Landing page
• Log in/ out
• 404 template
• Typography is emphasised
• Please use either a) typemarrow.com, b) free web fonts, c) brindle fonts
• All design elements in vector format
• Preferably with icons for each header title(i.e. about us, how it works etc) but designer have free reign over how the site looks, so might not be applicable
• All pages to be responsive
• Down to eSlab resolution

High level visual design brief attached - additional pages to be worked from base design.

Design inspiration
• We would like to use design elements from the following sources:
http://www.zandrix.com/halcyon/ (Functionality)
Colour scheme refer to logo and complementary style guide

```html
<!DOCTYPE html>
<html lang="en">
<head>
<meta charset="utf-8">
<title>Roast Harbor</title>
<link href="https://fonts.googleapis.com/css2?family=Open+Sans:wght@400;600;800&display=swap" rel="stylesheet">
<style>
  :root {
    --cream: #f6f5ea;
    --orange: #f7941d;
    --orange-light: #fbac3e;
    --ink: #111111;
    --black: #000000;
    --white: #ffffff;
    --footer-link: #6f6f6f;
    --icon-grey: #7a7a7a;
    --divider: #d8811a;
  }
  * { margin: 0; padding: 0; box-sizing: border-box; }
  html, body { width: 1200px; height: 899px; overflow: hidden; }
  body { font-family: "Open Sans", Arial, sans-serif; background: var(--black); position: relative; }

  .site-header {
    position: absolute; left: 0; top: 0; width: 1200px; height: 77px;
    background: var(--cream);
  }
  .brand {
    position: absolute; left: 56px; top: 24px;
    display: flex; align-items: center; gap: 8px;
    font-weight: 800; font-size: 19px; letter-spacing: 0.4px; color: var(--ink);
  }
  .brand-mark { width: 28px; height: 28px; border-radius: 50%; background: var(--orange); }
  .account-nav {
    position: absolute; left: 962px; top: 22px; height: 34px; width: 150px;
    display: flex; border-radius: 17px; background: var(--orange); overflow: hidden;
  }
  .account-nav a {
    flex: 1; display: flex; align-items: center; justify-content: center;
    color: var(--white); text-decoration: none; font-size: 14px;
  }
  .account-nav a + a { border-left: 1px solid var(--divider); }

  .hero { position: absolute; left: 0; top: 77px; width: 1200px; height: 680px; overflow: hidden; }
  .hero-photo {
    position: absolute; inset: 0;
    background:
      radial-gradient(ellipse 360px 260px at 820px 230px, rgba(232,178,120,0.95) 0%, rgba(200,130,70,0) 100%),
      radial-gradient(ellipse 260px 300px at 230px 380px, rgba(214,110,40,0.7) 0%, rgba(160,80,30,0) 100%),
      linear-gradient(180deg, #6a3a1c 0%, #9a6438 38%, #7a4826 62%, #3d2312 82%, #1c0f07 100%);
  }
  .hero-copy { position: absolute; left: 708px; top: 281px; }
  .hero-title {
    color: var(--orange); font-size: 33px; line-height: 36px; font-weight: 400;
  }
  .hero-subtitle {
    color: var(--white); font-size: 23.5px; line-height: 28px; font-weight: 400; white-space: nowrap;
  }
  .watch-video {
    position: absolute; left: -1px; top: 78px; width: 141px; height: 37px;
    border-radius: 19px; background: var(--black); color: var(--orange-light);
    display: flex; align-items: center; justify-content: center; gap: 10px;
    font-size: 12px; text-decoration: none;
  }

  .site-footer { position: absolute; left: 0; top: 757px; width: 1200px; height: 142px; background: var(--black); }
  .footer-col { position: absolute; top: 24px; }
  .footer-col h3 { color: var(--orange); font-size: 13.5px; font-weight: 400; margin-bottom: 15px; }
  .footer-col a { display: block; color: var(--footer-link); font-size: 12.5px; line-height: 15px; text-decoration: none; }
  .col-info { left: 54px; }
  .col-who { left: 217px; }
  .social { position: absolute; left: 925px; top: 22px; display: flex; align-items: center; }
  .social span { color: var(--orange); font-size: 13.5px; margin-right: 10px; }
  .social i { display: block; width: 30px; height: 30px; border-radius: 50%; background: var(--icon-grey); margin-right: 5px; }
  .legal { position: absolute; right: 57px; top: 108px; color: var(--footer-link); font-size: 12px; }
</style>
</head>
<body>
  <header class="site-header">
    <div class="brand"><span class="brand-mark"></span>ROAST HARBOR</div>
    <nav class="account-nav"><a href="#">LOGIN</a><a href="#">SIGNUP</a></nav>
  </header>

  <section class="hero">
    <div class="hero-photo" role="img" aria-label="Photograph of a wooden coffee grinder, a burlap sack of coffee beans, scattered beans, cinnamon sticks and a white cup on a bamboo mat against warm brown cloth"></div>
    <div class="hero-copy">
      <h1 class="hero-title">AUSTRALIA’S</h1>
      <p class="hero-subtitle">FIRST ONLINE COFFEE MARKETPLACE</p>
      <a class="watch-video" href="#">
        <svg width="12" height="14" viewBox="0 0 12 14"><path d="M0 0 L12 7 L0 14 Z" fill="#fbac3e"/></svg>
        WATCH VIDEO
      </a>
    </div>
  </section>

  <footer class="site-footer">
    <div class="footer-col col-info">
      <h3>HELPFUL INFO</h3>
      <a href="#">ABOUT US</a><a href="#">MEDIA ENQUIRIES</a><a href="#">TERMS &amp; CONDITIONS</a><a href="#">PRIVACY POLICY</a>
    </div>
    <div class="footer-col col-who">
      <h3>WHO WE ARE</h3>
      <a href="#">HOW IT WORKS</a><a href="#">FAQ</a><a href="#">CONTACT US</a>
    </div>
    <div class="social"><span>JOIN US ON</span><i></i><i></i><i></i><i></i></div>
    <p class="legal">COPYRIGHT © 2014 ROAST HARBOR | &nbsp;ALL RIGHTS RESERVED &nbsp;| PRIVACY POLICY</p>
  </footer>
</body>
</html>
```